Velkora Land Surveying Website Design

We are working with Velkora. They are a national land surveying company and in need of a new website design.

Some sites to use for inspiration:

https://brannickeng.com
https://www.dvwinc.com
https://kelvarin.com
https://gto.us
https://ravendobuilt.com
https://www.marbeckquillondale.com

Thank you for taking the time to consider designing a website for us. We are web developers based in Stockton and Los Angeles, CA, USA. Most of our projects go through the same process. Understanding this process may help you win a project with us. We custom-code all of our websites in-house. We don’t have any requirements as to what tools you use for your design, but we prefer Figma files. For any design that we label as four-stars, we send it to the client for review. The client picks the final design they want us to use. Once we complete this process, we will continue to show additional clients all the four-star sites and purchase them later. Your designs will have multiple chances to sell. For better chances of success, we ask that you follow these guidelines.

IMAGES:
If you use any images or icons in the design, we ask that you have a link to the asset so we can purchase the image/icon. Most of the designs we submit do not have the customer’s images on them unless they have some great images. Be creative; show us the feeling you are trying to portray with your image choices. Use any royalty-free site you choose. We subscribe to Pellix and mainly use their images, but we can purchase images outside of Pellix.

PLEASE NOTE: we will not submit designs to clients with watermarks on the images.

FONTS:
We ask that you identify the fonts used in the design. This can be done in a message if you want. We typically use Google Fonts and Pellix Fonts.

CONTENT:
We're always open to different content and ideas. We often submit designs with stock images so the client can see our vision. We typically take pictures after the website launch to use their images with our vision. Lorem Ipsum is fine for paragraphs, but we ask that you write the headers in correct English. We want to be able to show the vision and identify the sections of the website.

INSPIRATION:
We typically add a couple of links in the brief of websites we like to help you get started in your design.

REVISIONS:
We do not often ask for revisions of the designs unless we see something in the design that may not appeal to the client. If there are slight changes that we want to make, we do that in the development process.

FEEDBACK:
We rarely give feedback on designs during the design process. We are working on many website projects and do not have the time to provide feedback. We usually respond if your request is well thought out and asks specific questions, but a note asking “feedback, please” usually goes unanswered.

```html
<!DOCTYPE html>
<html lang="en">
<head>
<meta charset="utf-8">
<title>Velkora Land Surveying</title>
<link href="https://fonts.googleapis.com/css2?family=Oswald:wght@400;500;600;700&family=Rajdhani:wght@400;500;600;700&display=swap" rel="stylesheet">
<style>
:root{
  --red:#c9302c;
  --red-dark:#a82622;
  --slate:#5a5f5e;
  --ink:#2f3232;
  --footer:#2c2e2e;
  --paper:#f6f6f5;
  --card-grey:#dde0dc;
  --text:#4a4d4d;
  --white:#ffffff;
}
*{margin:0;padding:0;box-sizing:border-box}
html,body{width:1200px;height:5305px;overflow:hidden}
body{position:relative;background:var(--paper);font-family:'Rajdhani',sans-serif;color:var(--text)}
.abs{position:absolute}
.heading{font-family:'Oswald',sans-serif;font-weight:600;text-transform:uppercase;letter-spacing:.5px}
.btn{position:absolute;display:flex;align-items:center;justify-content:center;background:var(--red);color:var(--white);font-family:'Rajdhani',sans-serif;font-weight:700;font-size:16px;letter-spacing:.5px;text-transform:uppercase;border-radius:6px}
.media{position:absolute}

/* header */
.site-header{position:absolute;left:0;top:0;width:1200px;height:125px;z-index:5;border-top:4px solid var(--red)}
.brand{position:absolute;left:144px;top:38px;display:flex;align-items:center;gap:12px}
.brand-dot{width:46px;height:46px;border-radius:50%;background:var(--red)}
.brand-name{font-family:'Oswald',sans-serif;font-weight:600;font-size:24px;color:var(--red);line-height:1;text-transform:uppercase}
.brand-name small{display:block;font-size:12px;letter-spacing:2px;margin-top:3px}
.main-nav{position:absolute;left:420px;top:56px;display:flex;gap:26px;font-size:14px;font-weight:600;color:var(--ink);text-transform:uppercase}
.main-nav .active{border-bottom:2px solid var(--red);padding-bottom:4px}

/* hero */
.hero-photo{left:0;top:0;width:1200px;height:823px;background:linear-gradient(100deg,#b4493a 0%,#c88867 25%,#b7b1a6 55%,#9a9585 80%,#7f735a 100%)}
.hero-title{position:absolute;left:609px;top:190px;font-size:51px;line-height:61px;color:var(--red)}
.hero-title .dark{color:var(--ink)}
.hero-sub{position:absolute;left:609px;top:386px;width:420px;font-size:23px;line-height:32px;color:var(--ink);font-weight:500}
.hero-dots{position:absolute;left:1114px;top:658px;display:flex;flex-direction:column;gap:12px}
.hero-dots span{width:8px;height:8px;border-radius:50%;background:var(--white)}
.hero-dots span:first-child{background:var(--red)}

/* services */
.section-title{position:absolute;left:0;width:1200px;text-align:center;font-size:52px;color:var(--ink)}
.section-title em{font-style:normal;color:var(--red)}
.service{position:absolute;width:296px;height:305px}
.service-card{display:flex;flex-direction:column;align-items:center;justify-content:center;text-align:center;padding:0 28px;background:var(--card-grey);color:var(--ink)}
.service-card h3{font-family:'Rajdhani',sans-serif;font-weight:700;font-size:22px;line-height:32px;text-transform:uppercase;margin-bottom:14px}
.service-card p{font-size:15px;line-height:25px;color:#7b7f7e}
.service-card a{margin-top:12px;font-size:14px;font-weight:700;color:var(--red);text-decoration:underline;text-transform:uppercase}
.service-card.featured{background:var(--red);color:var(--white)}
.service-card.featured p,.service-card.featured a{color:#f6dcda}
.service-card.featured::after{content:"";position:absolute;left:50%;bottom:-1px;margin-left:-11px;border:11px solid transparent;border-bottom-color:var(--paper)}

/* about */
.about-title{position:absolute;left:646px;top:1855px;font-size:52px;color:var(--white)}
.about-title em{font-style:normal;color:var(--red)}
.about-text{position:absolute;left:646px;top:1943px;width:410px;font-size:15px;line-height:30.5px;color:#e4e6e5;text-align:justify}
.emblem{position:absolute;left:200px;top:1850px;width:320px;height:320px;border-radius:50%;border:8px solid var(--white);display:flex;align-items:center;justify-content:center;font-family:'Oswald',sans-serif;font-size:46px;font-weight:600;color:var(--white);text-transform:uppercase}

/* projects */
.projects-sub{position:absolute;left:0;top:2531px;width:1200px;text-align:center;font-size:24px;font-weight:500;color:var(--ink)}
.project-photo{position:absolute;top:2624px;height:380px}
.project-card{position:absolute;top:2916px;width:310px;height:165px;background:var(--white);padding:28px 32px;box-shadow:0 2px 10px rgba(0,0,0,.08)}
.project-card.active{border:1px solid #cfd2d1}
.project-card h3{font-size:20px;font-weight:700;color:var(--ink);margin-bottom:12px}
.project-card p{font-size:14px;line-height:23px;color:#777b7a;text-align:justify}
.project-arrow{position:absolute;right:-1px;bottom:-1px;width:48px;height:40px;background:var(--red);border-radius:28px 0 0 0;display:flex;align-items:center;justify-content:center}

/* stats */
.stats{position:absolute;left:0;top:3293px;width:498px;height:607px}
.stats-top{position:absolute;left:0;top:0;width:498px;height:308px;background:var(--red)}
.stats-bottom{position:absolute;left:0;top:308px;width:498px;height:299px;background:var(--slate)}
.stat{position:absolute;left:144px;display:flex;gap:36px;color:var(--white)}
.stat svg{margin-top:4px}
.stat-label{font-size:21px;font-weight:500;text-transform:uppercase;color:#f1e0df;line-height:26px}
.stat-value{font-size:22px;font-weight:700;line-height:34px}
.video{left:498px;top:3293px;width:702px;height:607px;background:linear-gradient(180deg,#8f9aa4 0%,#6f8570 18%,#4a8a3d 45%,#3f8a39 70%,#4d8640 100%)}
.play{position:absolute;left:806px;top:3564px;width:70px;height:70px;border-radius:50%;background:var(--white);display:flex;align-items:center;justify-content:center}

/* testimonials */
.testimonial{position:absolute;top:4168px;width:300px;height:175px;background:var(--white);text-align:center;padding:16px 12px}
.testimonial.active{border:1px solid #d6d8d7;border-bottom:3px solid var(--red)}
.testimonial.active::after{content:"";position:absolute;left:50%;bottom:-14px;margin-left:-9px;border:9px solid transparent;border-top-color:var(--red);border-bottom:0}
.quote-mark{font-family:'Oswald',sans-serif;font-size:60px;line-height:50px;color:var(--red);height:38px;overflow:hidden}
.testimonial p{font-size:12.5px;line-height:22px;color:#6e7271;margin-top:6px}
.person{position:absolute;top:4368px;display:flex;align-items:center;gap:10px}
.avatar{width:42px;height:42px;border-radius:50%;background:#8d8f8e}
.person b{display:block;font-size:16px;color:var(--ink)}
.person small{font-size:11px;color:#777}
.slider-dots{position:absolute;left:574px;top:4462px;display:flex;gap:12px}
.slider-dots span{width:7px;height:7px;border-radius:50%;background:#b9bbba}
.slider-dots span:first-child{background:var(--red)}

/* cta + footer */
.site-footer{position:absolute;left:0;top:4590px;width:1200px;height:715px;background:var(--footer)}
.cta{position:absolute;left:144px;top:4558px;width:910px;height:280px;background:var(--red);border-radius:140px}
.cta-mark{position:absolute;left:50px;top:40px;width:200px;height:200px;border-radius:50%;border:7px solid var(--white);display:flex;align-items:center;justify-content:center;font-family:'Oswald',sans-serif;font-size:32px;font-weight:600;color:var(--white);text-transform:uppercase}
.cta h2{position:absolute;left:338px;top:52px;font-size:42px;line-height:60px;color:var(--white)}
.footer-col{position:absolute;top:4925px;border-left:2px solid var(--red);height:225px;padding-left:32px;color:#d5d7d6}
.footer-col h4{font-family:'Rajdhani',sans-serif;font-weight:700;font-size:22px;color:var(--white);text-transform:uppercase;margin-bottom:18px}
.footer-col li{list-style:none;font-size:16px;line-height:27.5px}
.contact-row{display:flex;gap:14px;font-size:16px;line-height:24px;margin-bottom:20px}
.input{width:265px;height:48px;background:var(--white);border-radius:4px;font-size:14px;color:#555;padding:14px 26px;margin-top:16px}
.subscribe{position:static;width:265px;height:48px;margin-top:14px}
.footer-rule{position:absolute;left:0;top:5218px;width:1200px;height:1px;background:#434646}
.copyright{position:absolute;left:0;top:5244px;width:1200px;text-align:center;font-size:16px;color:#cfd1d0}
</style>
</head>
<body>

<header class="site-header">
  <div class="brand"><span class="brand-dot"></span><div class="brand-name">Velkora<small>Land Surveying</small></div></div>
  <nav class="main-nav">
    <span class="active">Home</span><span>Services</span><span>Industries</span><span>Projects</span><span>About</span><span>Contact</span>
  </nav>
  <div class="btn" style="left:883px;top:41px;width:171px;height:44px;font-size:14px">Request a Quote</div>
</header>

<section class="hero">
  <div class="media hero-photo" role="img" aria-label="Surveyor in a high-visibility vest using a total station on a construction site"></div>
  <h1 class="heading hero-title">National Land<br><span class="dark">Surveying with</span><br>Precision &amp; Expertise</h1>
  <p class="hero-sub">Serving government, commercial, and private clients across the U.S</p>
  <div class="btn" style="left:611px;top:488px;width:206px;height:48px">Request a Quote</div>
  <div class="hero-dots"><span></span><span></span><span></span></div>
  <svg class="abs" style="left:0;top:690px" width="1200" height="140" viewBox="0 0 1200 140">
    <path d="M0 140 V120 Q600 -20 1200 120 V140 Z" fill="var(--paper)"/>
    <path d="M330 46 Q600 10 870 46" fill="none" stroke="var(--red)" stroke-width="14"/>
  </svg>
</section>

<h2 class="heading section-title" style="top:855px"><em>Key</em> Services</h2>
<div class="service media" style="left:144px;top:972px" role="img" aria-label="Surveyor placing a marker stake in the ground"><div style="width:100%;height:100%;background:linear-gradient(90deg,#c4442e,#8c5b3c 45%,#5f8a44)"></div></div>
<div class="service service-card featured" style="left:452px;top:972px">
  <h3>Construction<br>Layout &amp; Staking</h3>
  <p>Nemo enim ipsam voluptatem quia voluptas sit aspernatur aut odit aut fugit, sed quia sequuntur magni dolores</p>
  <a>Read More</a>
</div>
<div class="service media" style="left:760px;top:972px" role="img" aria-label="Survey drone flying over green farmland"><div style="width:100%;height:100%;background:linear-gradient(180deg,#a9b4b6,#5f8f4c 40%,#3f7d34)"></div></div>
<div class="service service-card" style="left:144px;top:1288px">
  <h3>Boundary &amp;<br>Topographic Surveys</h3>
  <p>Nemo enim ipsam voluptatem quia voluptas sit aspernatur aut odit aut fugit, sed quia sequuntur magni dolores</p>
  <a>Read More</a>
</div>
<div class="service media" style="left:452px;top:1288px" role="img" aria-label="Surveyor in protective suit on a marked-out field"><div style="width:100%;height:100%;background:linear-gradient(180deg,#9b978d,#b5b0a5 50%,#8d887d)"></div></div>
<div class="service service-card" style="left:760px;top:1288px">
  <h3>Drone &amp; Lidar<br>Mapping</h3>
  <p>Nemo enim ipsam voluptatem quia voluptas sit aspernatur aut odit aut fugit, sed quia sequuntur magni dolores</p>
  <a>Read More</a>
</div>

<section class="about">
  <svg class="abs" style="left:0;top:1605px" width="1200" height="731" viewBox="0 0 1200 731">
    <path d="M0 0 Q300 150 620 140 Q900 130 1200 30 V731 H0 Z" fill="var(--slate)"/>
    <path d="M0 0 Q300 150 620 140 L520 165 L0 731 Z" fill="var(--red)"/>
    <path d="M0 40 Q300 170 620 160 L520 165 L0 731 Z" fill="var(--red)"/>
    <path d="M0 0 Q300 150 620 140 Q900 130 1200 30" fill="none" stroke="var(--paper)" stroke-width="16"/>
    <path d="M410 146 Q600 150 800 126" fill="none" stroke="var(--red)" stroke-width="12"/>
  </svg>
  <div class="emblem">Velkora</div>
  <h2 class="heading about-title">About <em>Us</em></h2>
  <p class="about-text">Sed ut perspiciatis unde omnis iste natus error sit voluptatem accusantium doloremque laudantium, totam rem aperiam, eaque ipsa quae ab illo inventore veritatis et quasi architecto beatae vitae dicta sunt explicabo. Nemo enim ipsam voluptatem quia voluptas sit aspernatur aut odit aut fugit, sed quia consequuntur magni dolores eos qui ratione vo et dolore magnam aliquam quaerat voluptatem.</p>
  <div class="btn" style="left:646px;top:2183px;width:176px;height:48px">Read More</div>
</section>

<section class="projects">
  <h2 class="heading section-title" style="top:2445px"><em>Our</em> Projects</h2>
  <p class="projects-sub">Projects that reflect our Purpose</p>
  <div class="project-photo media" style="left:0;width:366px;background:linear-gradient(180deg,#9aa0a4,#6e6a62 55%,#4c4842)" role="img" aria-label="Survey crew with tripods on a construction site"></div>
  <div class="project-photo media" style="left:399px;width:402px;background:linear-gradient(180deg,#8f8a80,#a8a194 50%,#7f786c)" role="img" aria-label="Marking a survey point with spray paint on gravel"></div>
  <div class="project-photo media" style="left:833px;width:367px;background:linear-gradient(180deg,#9b8c82,#6a6d63 55%,#7a4a3a)" role="img" aria-label="Engineers in hard hats reviewing site plans"></div>
  <article class="project-card" style="left:4px">
    <h3>Sed ut perspe omnisist</h3>
    <p>Nemo enim ipsam voluptatem quia voluptas sit aspernatur aut odit aut fugit, sed quia consequuntur</p>
    <span class="project-arrow"><svg width="16" height="16" viewBox="0 0 16 16"><path d="M5 2l6 6-6 6" fill="none" stroke="#fff" stroke-width="2.5"/></svg></span>
  </article>
  <article class="project-card active" style="left:437px">
    <h3>Sed ut perspe omnisist</h3>
    <p>Nemo enim ipsam voluptatem quia voluptas sit aspernatur aut odit aut fugit, sed quia consequuntur</p>
    <span class="project-arrow"><svg width="16" height="16" viewBox="0 0 16 16"><path d="M5 2l6 6-6 6" fill="none" stroke="#fff" stroke-width="2.5"/></svg></span>
  </article>
  <article class="project-card" style="left:872px">
    <h3>Sed ut perspe omnisist</h3>
    <p>Nemo enim ipsam voluptatem quia voluptas sit aspernatur aut odit aut fugit, sed quia consequuntur</p>
    <span class="project-arrow"><svg width="16" height="16" viewBox="0 0 16 16"><path d="M5 2l6 6-6 6" fill="none" stroke="#fff" stroke-width="2.5"/></svg></span>
  </article>
  <div class="btn" style="left:443px;top:3144px;width:314px;height:50px">View More Projects</div>
</section>

<section class="stats">
  <div class="stats-top"></div>
  <div class="stats-bottom"></div>
  <div class="stat" style="top:73px">
    <svg width="30" height="30" viewBox="0 0 24 24"><path d="M3 21l1-5L16 4l4 4L8 20z" fill="#fff"/></svg>
    <div><div class="stat-label">Projects</div><div class="stat-value">90,000+</div></div>
  </div>
  <div class="stat" style="top:181px">
    <svg width="30" height="30" viewBox="0 0 24 24"><path d="M2 5l6-2 8 3 6-2v15l-6 2-8-3-6 2z" fill="#fff"/><path d="M8 3v15M16 6v15" stroke="var(--red)" stroke-width="1.5"/></svg>
    <div><div class="stat-label">Countries Worked In</div><div class="stat-value">150+</div></div>
  </div>
  <div class="stat" style="top:380px">
    <svg width="30" height="30" viewBox="0 0 24 24"><path d="M5 2v20" stroke="#fff" stroke-width="2"/><path d="M6 3h13l-3 5 3 5H6z" fill="#fff"/></svg>
    <div><div class="stat-label">Languages Spoken</div><div class="stat-value">90,000+</div></div>
  </div>
  <div class="stat" style="top:488px">
    <svg width="34" height="30" viewBox="0 0 28 24"><circle cx="14" cy="7" r="4" fill="#fff"/><circle cx="5" cy="9" r="3" fill="#fff"/><circle cx="23" cy="9" r="3" fill="#fff"/><path d="M7 20a7 7 0 0114 0z M0 20a5 5 0 019-3 M28 20a5 5 0 00-9-3" fill="#fff"/></svg>
    <div><div class="stat-label">LEED Professionals</div><div class="stat-value">150+</div></div>
  </div>
</section>
<div class="media video" role="img" aria-label="Aerial view of a survey drone mapping green fields"></div>
<div class="play"><svg width="26" height="26" viewBox="0 0 24 24"><path d="M8 5v14l11-7z" fill="var(--red)"/></svg></div>

<section class="testimonials">
  <h2 class="heading section-title" style="top:4022px"><em>Client</em> Testimonials</h2>
  <blockquote class="testimonial" style="left:0"><div class="quote-mark">&ldquo;</div><p>"Lorem ipsum dolor sit amet, consectetur adipiscing elit, sed do eiusmod tempor incididunt ut labore et dolore magna aliqu enim ad minim veniam,ullamco laboris nisi ut aliquip ex ea commodoullamco"</p></blockquote>
  <blockquote class="testimonial active" style="left:292px"><div class="quote-mark">&ldquo;</div><p>"Lorem ipsum dolor sit amet, consectetur adipiscing elit, sed do eiusmod tempor incididunt ut labore et dolore magna aliqu enim ad minim veniam,ullamco laboris nisi ut aliquip ex ea commodoullamco"</p></blockquote>
  <blockquote class="testimonial" style="left:611px"><div class="quote-mark">&ldquo;</div><p>"Lorem ipsum dolor sit amet, consectetur adipiscing elit, sed do eiusmod tempor incididunt ut labore et dolore magna aliqu enim ad minim veniam,ullamco laboris nisi ut aliquip ex ea commodoullamco"</p></blockquote>
  <blockquote class="testimonial" style="left:924px"><div class="quote-mark">&ldquo;</div><p>"Lorem ipsum dolor sit amet, consectetur adipiscing elit, sed do eiusmod tempor incididunt ut labore et dolore magna aliqu enim ad minim veniam,ullamco laboris nisi ut aliquip ex ea commodoullamco"</p></blockquote>
  <div class="person" style="left:54px"><span class="avatar" role="img" aria-label="Client portrait"></span><div><b>Owen Hale</b><small>Site Manager</small></div></div>
  <div class="person" style="left:366px"><span class="avatar" role="img" aria-label="Client portrait"></span><div><b>Rita Calloway</b><small>Site Manager</small></div></div>
  <div class="person" style="left:690px"><span class="avatar" role="img" aria-label="Client portrait"></span><div><b>Dario Venturi</b><small>Site Manager</small></div></div>
  <div class="person" style="left:1024px"><span class="avatar" role="img" aria-label="Client portrait"></span><div><b>Dario Venturi</b><small>Site Manager</small></div></div>
  <div class="slider-dots"><span></span><span></span><span></span></div>
</section>

<footer class="site-footer"></footer>
<svg class="abs" style="left:0;top:4540px" width="1200" height="90" viewBox="0 0 1200 90"><path d="M0 20 Q600 110 1200 20 V90 H0 Z" fill="var(--footer)"/></svg>
<section class="cta">
  <div class="cta-mark">Velkora</div>
  <h2 class="heading">Get your next project off<br>to a precise start.</h2>
  <div class="btn" style="left:338px;top:190px;width:268px;height:46px;background:var(--slate)">Request a Quote Today</div>
</section>

<div class="footer-col" style="left:160px">
  <h4>Contact Us</h4>
  <div class="contact-row"><svg width="16" height="16" viewBox="0 0 24 24" style="margin-top:4px"><path d="M2 5l6-2 8 3 6-2v15l-6 2-8-3-6 2z" fill="var(--red)"/></svg><span>233,Nemo enim ioluptatem<br>quia voluptapernatur</span></div>
  <div class="contact-row"><svg width="16" height="16" viewBox="0 0 24 24" style="margin-top:4px"><path d="M6 2l4 4-2 3a12 12 0 007 7l3-2 4 4-3 4C10 22 2 14 2 5z" fill="var(--red)"/></svg><span style="color:#fff;font-weight:600;font-size:18px">+1 555 014 2290</span></div>
  <div class="contact-row"><svg width="16" height="16" viewBox="0 0 24 24" style="margin-top:4px"><path d="M2 5h20v14H2z" fill="var(--red)"/><path d="M2 5l10 8 10-8" fill="none" stroke="var(--footer)" stroke-width="2"/></svg><span>hello@velkoramail.com</span></div>
</div>
<div class="footer-col" style="left:495px">
  <h4>Quick Links</h4>
  <ul><li>Home</li><li>Services</li><li>Industries</li><li>Projects</li><li>About</li><li>Contact</li></ul>
</div>
<div class="footer-col" style="left:742px">
  <h4>Sign up to Newsltter</h4>
  <p style="font-size:16px">Nemo enim ipsam voluptatem quia</p>
  <div class="input">Enter Email</div>
  <div class="btn subscribe">Subscribe</div>
</div>
<div class="footer-rule"></div>
<p class="copyright">&copy; 2025 Velkora. All Rights Reserved &nbsp;|&nbsp; Privacy Policy &nbsp;|&nbsp; Terms of Use</p>

</body>
</html>
```